Tessmar Fahrwerkstatt
Sehr angenehme zusammenarbeit nicht aufdringlich und genau auf die Wünsche eingegangen. Wir werde sicher noch mehr zusammen Arbeiten. Gruss Lukas Hegemann Inhaber Tessmar Fahrwerkstatt
Zielgruppe
Dinks und Kunden mit viel Erfolg und hohem Ausgabepotential.
Aufgabenstellung
Unsere Firma vertreibt Fahrzeuge im Luxusbereich hauptgebiet Valmerra aber auch andere Sportwagen. Was uns fehlt ist ein optischer Wiedererkennugswert. Deshalb hätten wir gerne ein Visitenkarten Design und Briefpapier Design. Später soll auch noch eine Webseite mit gleichem Wiedererkennungswert entstehen. " Roter Faden "

```html
<!DOCTYPE html>
<html lang="de">
<head>
<meta charset="utf-8">
<title>Tessmar Fahrwerkstatt – Visitenkarte</title>
<link rel="stylesheet" href="https://fonts.googleapis.com/css2?family=Noto+Serif:wght@700&family=Noto+Sans:wght@700&display=swap">
<style>
  :root {
    --card-bg: #3d3d3d;
    --edge-band: #8a8a8a;
    --text-light: #f4f4f4;
    --mark-tone: #ffffff;
    --backdrop-tone: #b9ada1;
  }
  html, body {
    margin: 0;
    padding: 0;
    width: 1200px;
    height: 777px;
    overflow: hidden;
    background: var(--card-bg);
  }
  .card {
    position: relative;
    width: 1200px;
    height: 777px;
    background: var(--card-bg);
    overflow: hidden;
  }
  .backdrop-tone {
    position: absolute;
    left: 470px;
    top: 0;
    width: 730px;
    height: 777px;
  }
  .edge-band {
    position: absolute;
    left: 451px;
    top: 0;
    width: 749px;
    height: 5px;
    background: var(--edge-band);
  }
  .brand-mark {
    position: absolute;
    left: 62px;
    top: 56px;
    width: 168px;
    height: 168px;
  }
  .company-name {
    position: absolute;
    left: 255px;
    top: 166px;
    margin: 0;
    font-family: "Noto Serif", serif;
    font-weight: 700;
    font-size: 50px;
    line-height: 1;
    color: var(--text-light);
    white-space: nowrap;
  }
  .job-title {
    position: absolute;
    left: 516px;
    top: 337px;
    margin: 0;
    font-family: "Noto Sans", sans-serif;
    font-weight: 700;
    font-size: 45px;
    line-height: 1;
    letter-spacing: 0.5px;
    color: var(--text-light);
    white-space: nowrap;
  }
</style>
</head>
<body>
  <main class="card">
    <svg class="backdrop-tone" viewBox="0 0 730 777" role="img" aria-label="Große, blasse Hintergrundfläche im Taupe-Ton der Marke">
      <defs>
        <radialGradient id="backdrop-glow" cx="0.55" cy="0.5" r="0.6">
          <stop offset="0" stop-color="var(--backdrop-tone)" stop-opacity="0.38"/>
          <stop offset="0.6" stop-color="var(--backdrop-tone)" stop-opacity="0.16"/>
          <stop offset="1" stop-color="var(--backdrop-tone)" stop-opacity="0"/>
        </radialGradient>
      </defs>
      <rect width="730" height="777" fill="url(#backdrop-glow)"/>
    </svg>
    <div class="edge-band"></div>
    <svg class="brand-mark" viewBox="0 0 150 150" aria-hidden="true">
      <circle cx="75" cy="75" r="70" fill="none" stroke="var(--mark-tone)" stroke-width="6"/>
    </svg>
    <h1 class="company-name">Tessmar Fahrwerkstatt</h1>
    <p class="job-title">Sales representative</p>
  </main>
</body>
</html>
```